Skin cancer clinic services trifold brochure

Need trifold brochure listing skin cancer services our clinic provides, staff information, location and brief about skin cancer with colours similar to our web site www.Tolvarin.clinic. I will provide more information regarding services and staff but want this colourful and standout as it will be given to other referring doctors or patients

Target Market(s)

Age 40 to 80 years

Industry/Entity Type

Medical

Font styles to use
Serif

Colors

Designer to choose colors to be used in the design.

Requirements
Must have
• Logo, services, contact info, beach or sun look and colours similar to web site or logo

```html
<!DOCTYPE html>
<html lang="en">
<head>
<meta charset="utf-8">
<title>Tolvarin Skin Cancer Clinic – Trifold Brochure</title>
<link rel="stylesheet" href="https://fonts.googleapis.com/css2?family=Cinzel:wght@600;700&family=Kaushan+Script&family=Open+Sans:wght@400;600;700&family=Playfair+Display:ital,wght@0,700;1,400&display=swap">
<style>
:root{
  --orange:#f0921c;
  --gold:#f7b52c;
  --blue:#2c8fd2;
  --blue-dark:#1f6fae;
  --white:#ffffff;
  --paper:#fbfbfb;
  --ink:#3a3a3a;
  --stage:#e4e4e4;
}
*{box-sizing:border-box;margin:0;padding:0}
html,body{width:1200px;height:2402px;overflow:hidden}
body{background:var(--stage);font-family:"Open Sans",Arial,sans-serif;color:var(--white)}
.spread{position:absolute;left:30px;width:1140px;height:880px;display:flex;box-shadow:0 18px 40px rgba(0,0,0,.22)}
.spread--outside{top:190px}
.spread--inside{top:1330px}
.panel{position:relative;width:380px;height:100%;overflow:hidden}
.panel--orange{background:linear-gradient(160deg,var(--gold) 0%,var(--orange) 100%)}
.panel--white{background:var(--paper);color:var(--ink)}
.photo{position:absolute;left:0;width:100%}
.wave{position:absolute;left:0;width:100%;display:block}
.pill-heading{display:inline-block;background:var(--blue);color:var(--white);font-family:"Cinzel",Georgia,serif;font-weight:700;font-size:17px;letter-spacing:.5px;padding:6px 28px 6px 22px;border-radius:0 20px 20px 0}
.body-copy{font-size:12.5px;line-height:1.55}
.serif-sub{font-family:"Playfair Display",Georgia,serif;font-style:italic;font-size:22px}
.brand{display:flex;align-items:center;justify-content:center;gap:10px;font-family:"Cinzel",Georgia,serif;font-weight:700;color:var(--ink)}
.brand__dot{width:22px;height:22px;border-radius:50%;background:var(--orange)}
.brand__name{font-size:40px;letter-spacing:1px}
.slogan{font-family:"Kaushan Script",cursive;color:var(--orange);font-size:30px;text-align:center}
.url-pill{display:block;background:var(--blue);color:var(--white);border-radius:22px;text-align:center;font-weight:600;letter-spacing:1px}
/* about flap */
.about{padding:34px 0 0}
.about .body-copy{padding:16px 30px 0}
.team{padding:14px 30px 0}
.team__title{margin-bottom:8px}
.team__member{list-style:none;margin-bottom:8px;padding-left:20px;position:relative}
.team__member::before{content:"";position:absolute;left:0;top:6px;width:9px;height:9px;border-radius:50%;background:var(--white)}
.team__name{font-family:"Playfair Display",Georgia,serif;font-weight:700;font-size:15px;display:block}
.team__role{font-size:11px;opacity:.9}
/* back panel */
.contact{text-align:center;padding-top:34px}
.contact .brand__name{font-size:30px;color:var(--white)}
.contact .brand__dot{background:var(--white);width:16px;height:16px}
.contact__heading{color:var(--blue-dark);font-family:"Cinzel",Georgia,serif;font-weight:700;font-size:18px;margin:22px 20px 10px}
.contact .body-copy{padding:0 34px;margin-bottom:8px}
.map{margin:14px auto 16px;width:300px;height:150px;background:linear-gradient(135deg,#f4f4f4,#dcdfe3);border-radius:4px}
.contact__book{font-family:"Cinzel",Georgia,serif;font-weight:700;font-size:21px;margin-bottom:8px}
.contact .url-pill{margin:0 40px 14px;font-size:16px;padding:7px}
.contact__line{font-size:14px;font-weight:600;line-height:1.6}
.social{display:flex;justify-content:center;gap:12px;margin-top:12px}
.social span{width:28px;height:28px;border-radius:50%;background:var(--white);opacity:.85}
/* cover */
.cover__brand{position:absolute;left:0;right:0;top:640px}
.cover__brand .brand__name{font-size:46px}
.cover .slogan{position:absolute;left:0;right:0;top:708px}
.cover .url-pill{position:absolute;left:36px;right:36px;top:780px;font-size:20px;padding:9px}
/* services */
.services{position:absolute;left:0;top:470px;width:100%}
.services__list{list-style:none;padding:18px 26px 0}
.services__item{display:flex;align-items:center;gap:12px;font-size:15px;font-weight:600;margin-bottom:11px}
.services__icon{width:22px;height:22px;border-radius:50%;border:2px solid var(--white);flex:none}
/* treatments */
.treatments{padding:30px 30px 0;text-align:center}
.treatments__title{color:var(--blue);font-family:"Cinzel",Georgia,serif;font-weight:700;font-size:22px;margin-bottom:10px}
.treatments__sub{color:var(--orange);font-family:"Cinzel",Georgia,serif;font-weight:700;font-size:15px;margin:16px 0 6px}
.treatments .body-copy{font-size:13.5px;line-height:1.65}
/* cosmetic */
.cosmetic{padding-top:34px}
.cosmetic .body-copy{padding:14px 30px 8px}
.check-list{list-style:none;padding:0 30px}
.check-list li{display:flex;align-items:center;gap:9px;font-size:13.5px;margin-bottom:6px;font-weight:600}
.check-list svg{flex:none}
.cosmetic__other{padding:10px 30px 6px}
.did-you-know{text-align:right;padding:12px 30px 0}
.did-you-know__title{font-family:"Cinzel",Georgia,serif;font-weight:700;font-size:19px;margin-bottom:4px}
.did-you-know .body-copy{font-size:12px}
.phone-pill{display:flex;align-items:center;justify-content:center;gap:10px;margin:14px 30px 6px;font-size:20px;padding:6px}
.cosmetic__url{text-align:center;font-weight:600;letter-spacing:1px;font-size:14px}
</style>
</head>
<body>

<!-- Outside of the brochure -->
<section class="spread spread--outside">

  <article class="panel panel--orange about">
    <h2 class="pill-heading">ABOUT TOLVARIN</h2>
    <p class="body-copy">Tolvarin is a leading skin cancer clinic serving the coast with caring doctors and modern tools.</p>
    <p class="body-copy">Headed by qualified practitioners in skin health, our team uses the latest technology to give every patient early answers.</p>
    <div class="team">
      <h3 class="serif-sub team__title">Introducing our Team...</h3>
      <ul>
        <li class="team__member"><span class="team__name">Dr. Marcus Elwood</span><span class="team__role">Skin cancer doctor</span></li>
        <li class="team__member"><span class="team__name">Dr. Priya Castell</span><span class="team__role">Skin cancer doctor</span></li>
        <li class="team__member"><span class="team__name">Dr. Owen Tarrant</span><span class="team__role">Skin cancer doctor</span></li>
        <li class="team__member"><span class="team__name">Renee Calder</span><span class="team__role">Registered practice nurse</span></li>
        <li class="team__member"><span class="team__name">Sophie Brandt</span><span class="team__role">Practice manager</span></li>
      </ul>
    </div>
    <div class="photo" style="top:640px;height:240px;background:linear-gradient(180deg,#7cc4ea 0%,#a9dcf2 45%,#e9d7b3 100%)" role="img" aria-label="Children playing in the sea at the beach"></div>
    <svg class="wave" style="top:620px" width="380" height="90" viewBox="0 0 380 90" aria-hidden="true">
      <path d="M0 0H380V20C300 20 220 90 120 80C70 75 30 55 0 60Z" fill="#f3a020"/>
      <path d="M0 60C30 55 70 75 120 80C220 90 300 20 380 20" fill="none" stroke="var(--blue)" stroke-width="6"/>
    </svg>
  </article>

  <article class="panel panel--orange contact">
    <div class="brand"><span class="brand__dot"></span><span class="brand__name">TOLVARIN</span></div>
    <h2 class="contact__heading">WHEN WAS YOUR LAST SKIN CHECK?</h2>
    <p class="body-copy">Welcome to a leading skin cancer clinic with friendly staff and fast results.</p>
    <p class="body-copy">Headed by qualified practitioners in skin health, we use the latest technology to spot skin cancer early.</p>
    <div class="map" role="img" aria-label="Street map showing the clinic location"></div>
    <p class="contact__book">BOOK AN APPOINTMENT</p>
    <span class="url-pill">www.Tolvarin.clinic</span>
    <p class="contact__line">Suites 1 &amp; 2 90 Harbour Road<br>Westbrook NSW 2260</p>
    <p class="contact__line">1300 555 014</p>
    <p class="contact__line">admin@tolvarin.clinic</p>
    <div class="social" aria-hidden="true"><span></span><span></span></div>
  </article>

  <article class="panel panel--white cover">
    <div class="photo" style="top:0;height:600px;background:linear-gradient(160deg,#c98a5c 0%,#8a5233 45%,#4a2a18 100%)" role="img" aria-label="Smiling woman with a sun drawn in sunscreen on her cheek"></div>
    <svg class="wave" style="top:430px" width="380" height="210" viewBox="0 0 380 210" aria-hidden="true">
      <path d="M0 150C120 170 260 120 380 0V210H0Z" fill="var(--paper)"/>
      <path d="M0 138C120 158 262 110 380 -8" fill="none" stroke="var(--gold)" stroke-width="12"/>
      <path d="M0 152C120 172 262 124 380 8" fill="none" stroke="var(--blue)" stroke-width="10"/>
    </svg>
    <div class="brand cover__brand"><span class="brand__dot"></span><span class="brand__name">TOLVARIN</span></div>
    <p class="slogan">“Care For Every Layer”</p>
    <span class="url-pill">www.Tolvarin.clinic</span>
  </article>
</section>

<!-- Inside of the brochure -->
<section class="spread spread--inside">

  <article class="panel panel--orange">
    <div class="photo" style="top:0;height:480px;background:linear-gradient(170deg,#6ec3e8 0%,#b9e2f2 40%,#d9a57c 100%)" role="img" aria-label="Woman in a sun hat with a sun drawn in sunscreen on her back"></div>
    <svg class="wave" style="top:380px" width="380" height="110" viewBox="0 0 380 110" aria-hidden="true">
      <path d="M0 40C120 20 260 90 380 60V110H0Z" fill="#f5a726"/>
      <path d="M0 40C120 20 260 90 380 60" fill="none" stroke="var(--blue)" stroke-width="6"/>
    </svg>
    <div class="services">
      <h2 class="pill-heading">OUR SERVICES</h2>
      <ul class="services__list">
        <li class="services__item"><span class="services__icon"></span>Skin cancer detection</li>
        <li class="services__item"><span class="services__icon"></span>Mole assessment</li>
        <li class="services__item"><span class="services__icon"></span>Digital monitoring of moles</li>
        <li class="services__item"><span class="services__icon"></span>Medical treatment of skin cancer</li>
        <li class="services__item"><span class="services__icon"></span>Surgical treatment of skin cancer</li>
        <li class="services__item"><span class="services__icon"></span>General dermatologic surgery</li>
        <li class="services__item"><span class="services__icon"></span>Same day ‘slow MOHs’ procedures</li>
      </ul>
    </div>
  </article>

  <article class="panel panel--white">
    <div class="treatments">
      <h2 class="treatments__title">TREATMENTS</h2>
      <h3 class="treatments__sub">EXCISION</h3>
      <p class="body-copy">Excision is the best treatment for most skin cancers. The spot is removed with a small margin of healthy skin under local anaesthetic and the wound is closed with fine stitches, giving a neat result.</p>
      <h3 class="treatments__sub">CURETTAGE</h3>
      <p class="body-copy">This traditional treatment is highly effective for many superficial skin cancers. The growth is gently scraped away and the base is sealed, leaving a small wound that heals quickly.</p>
      <h3 class="treatments__sub">CRYOTHERAPY</h3>
      <p class="body-copy">Cryotherapy, also known as cryosurgery, applies extreme cold directly to the skin. It is an effective treatment for sun spots and some early cancers, taking only seconds, and the area usually heals over the following weeks.</p>
    </div>
    <div class="photo" style="top:660px;height:220px;background:linear-gradient(180deg,#f3e4c8 0%,#e6c99a 100%)" role="img" aria-label="Person relaxing in a hammock on a sandy beach"></div>
    <svg class="wave" style="top:630px" width="380" height="80" viewBox="0 0 380 80" aria-hidden="true">
      <path d="M0 0H380V50C260 10 120 70 0 40Z" fill="var(--paper)"/>
      <path d="M0 40C120 70 260 10 380 50" fill="none" stroke="var(--blue)" stroke-width="6"/>
    </svg>
  </article>

  <article class="panel panel--orange cosmetic">
    <h2 class="pill-heading">COSMETIC SERVICES</h2>
    <p class="body-copy">Our mission is to help people with a range of skin concerns, with our advanced technology and caring team.</p>
    <ul class="check-list">
      <li><svg width="14" height="14" viewBox="0 0 14 14"><circle cx="7" cy="7" r="6.5" fill="#fff"/><path d="M4 7l2 2 4-4" stroke="var(--orange)" stroke-width="1.8" fill="none"/></svg>Moles</li>
      <li><svg width="14" height="14" viewBox="0 0 14 14"><circle cx="7" cy="7" r="6.5" fill="#fff"/><path d="M4 7l2 2 4-4" stroke="var(--orange)" stroke-width="1.8" fill="none"/></svg>Pigmentation</li>
      <li><svg width="14" height="14" viewBox="0 0 14 14"><circle cx="7" cy="7" r="6.5" fill="#fff"/><path d="M4 7l2 2 4-4" stroke="var(--orange)" stroke-width="1.8" fill="none"/></svg>Skin Rejuvenation</li>
      <li><svg width="14" height="14" viewBox="0 0 14 14"><circle cx="7" cy="7" r="6.5" fill="#fff"/><path d="M4 7l2 2 4-4" stroke="var(--orange)" stroke-width="1.8" fill="none"/></svg>Rosacea</li>
      <li><svg width="14" height="14" viewBox="0 0 14 14"><circle cx="7" cy="7" r="6.5" fill="#fff"/><path d="M4 7l2 2 4-4" stroke="var(--orange)" stroke-width="1.8" fill="none"/></svg>Wrinkles</li>
      <li><svg width="14" height="14" viewBox="0 0 14 14"><circle cx="7" cy="7" r="6.5" fill="#fff"/><path d="M4 7l2 2 4-4" stroke="var(--orange)" stroke-width="1.8" fill="none"/></svg>Acne Scarring</li>
      <li><svg width="14" height="14" viewBox="0 0 14 14"><circle cx="7" cy="7" r="6.5" fill="#fff"/><path d="M4 7l2 2 4-4" stroke="var(--orange)" stroke-width="1.8" fill="none"/></svg>Poor Skin Texture</li>
      <li><svg width="14" height="14" viewBox="0 0 14 14"><circle cx="7" cy="7" r="6.5" fill="#fff"/><path d="M4 7l2 2 4-4" stroke="var(--orange)" stroke-width="1.8" fill="none"/></svg>Unwanted Scars</li>
      <li><svg width="14" height="14" viewBox="0 0 14 14"><circle cx="7" cy="7" r="6.5" fill="#fff"/><path d="M4 7l2 2 4-4" stroke="var(--orange)" stroke-width="1.8" fill="none"/></svg>Skin Blemishes</li>
      <li><svg width="14" height="14" viewBox="0 0 14 14"><circle cx="7" cy="7" r="6.5" fill="#fff"/><path d="M4 7l2 2 4-4" stroke="var(--orange)" stroke-width="1.8" fill="none"/></svg>Sun Damaged Skin</li>
      <li><svg width="14" height="14" viewBox="0 0 14 14"><circle cx="7" cy="7" r="6.5" fill="#fff"/><path d="M4 7l2 2 4-4" stroke="var(--orange)" stroke-width="1.8" fill="none"/></svg>Hair Removal</li>
    </ul>
    <h3 class="serif-sub cosmetic__other">Other Devices and Services</h3>
    <ul class="check-list">
      <li><svg width="14" height="14" viewBox="0 0 14 14"><circle cx="7" cy="7" r="6.5" fill="#fff"/><path d="M4 7l2 2 4-4" stroke="var(--orange)" stroke-width="1.8" fill="none"/></svg>Anti Wrinkle Injections and Dermal fillers</li>
      <li><svg width="14" height="14" viewBox="0 0 14 14"><circle cx="7" cy="7" r="6.5" fill="#fff"/><path d="M4 7l2 2 4-4" stroke="var(--orange)" stroke-width="1.8" fill="none"/></svg>Ultratherapy</li>
      <li><svg width="14" height="14" viewBox="0 0 14 14"><circle cx="7" cy="7" r="6.5" fill="#fff"/><path d="M4 7l2 2 4-4" stroke="var(--orange)" stroke-width="1.8" fill="none"/></svg>Skin Needling</li>
      <li><svg width="14" height="14" viewBox="0 0 14 14"><circle cx="7" cy="7" r="6.5" fill="#fff"/><path d="M4 7l2 2 4-4" stroke="var(--orange)" stroke-width="1.8" fill="none"/></svg>Peels</li>
    </ul>
    <div class="did-you-know">
      <h3 class="did-you-know__title">DID YOU KNOW?</h3>
      <p class="body-copy">Skin cancer accounts for 80% of all newly diagnosed cancers. Get checked today.</p>
    </div>
    <span class="url-pill phone-pill">
      <svg width="20" height="20" viewBox="0 0 20 20" aria-hidden="true"><circle cx="10" cy="10" r="9" fill="none" stroke="#fff" stroke-width="1.5"/><path d="M7 5.5l1.6 2.4-1 1.1c.6 1.3 1.5 2.2 2.8 2.8l1.1-1 2.4 1.6-.8 1.6c-3.4-.3-6.6-3.5-6.9-6.9z" fill="#fff"/></svg>
      1300 555 014
    </span>
    <p class="cosmetic__url">www.Tolvarin.clinic</p>
  </article>
</section>

</body>
</html>
```